Puffy Clouds Cotton Candy

Looking for a logo design and business cards to help a 13 year old entrepreneur promote her cotton candy business.
Contact Information for Business Card
Name, Phone & Email
Colors
E54698
E96AAD
F1A4CE
F9D9EA
FCEFF6
A7469A
B969AE
D3A5CF
EDDBEB
F8F0F9
6B429C
8869AF
B7A5CE
E3DAEB
F3F0F8
Requirements
Must have
- A fun feel that is appropriate for a teenage girl selling cotton candy

```html
<!DOCTYPE html>
<html lang="en">
<head>
<meta charset="utf-8">
<title>Puffy Clouds Cotton Candy – Business Card</title>
<link rel="stylesheet" href="https://fonts.googleapis.com/css2?family=Poppins:wght@400;600&family=Arimo:wght@400&display=swap">
<style>
  :root {
    --pink: #E54698;
    --pink-light: #E96AAD;
    --purple: #6B429C;
    --purple-mid: #8869AF;
    --white: #FFFFFF;
    --divider: #C8C8C8;
    --stage: #2a2a2c;
  }
  * { margin: 0; padding: 0; box-sizing: border-box; }
  html, body { width: 1200px; height: 1015px; overflow: hidden; }
  body {
    background: var(--stage);
    font-family: "Poppins", sans-serif;
    display: flex;
    flex-direction: column;
    align-items: center;
    justify-content: center;
    gap: 40px;
  }
  .card {
    position: relative;
    width: 700px;
    height: 400px;
    overflow: hidden;
    box-shadow: 0 10px 30px rgba(0,0,0,.45);
  }

  /* Front side */
  .card-front {
    background: radial-gradient(ellipse 60% 75% at 50% 45%, var(--pink) 0%, #B1469B 40%, var(--purple) 100%);
    display: flex;
    flex-direction: column;
    align-items: center;
    justify-content: center;
    gap: 18px;
    color: var(--white);
  }
  .brand-disc {
    width: 150px;
    height: 150px;
    border-radius: 50%;
    border: 6px solid var(--white);
  }
  .brand-name {
    font-weight: 600;
    line-height: 1;
    text-align: center;
  }
  .brand-name .line-main { display: block; font-size: 44px; }
  .brand-name .line-sub { display: block; font-size: 32px; margin-top: 2px; }

  /* Back side */
  .card-back { background: var(--white); }
  .back-brand {
    position: absolute;
    left: 70px;
    top: 60px;
    width: 260px;
    display: flex;
    flex-direction: column;
    align-items: center;
    gap: 14px;
    color: var(--pink);
  }
  .back-brand .brand-disc { width: 130px; height: 130px; border-color: var(--pink); }
  .back-brand .line-main { font-size: 40px; }
  .back-brand .line-sub { font-size: 29px; }

  .divider {
    position: absolute;
    left: 370px;
    top: 80px;
    width: 1px;
    height: 130px;
    background: var(--divider);
  }
  .contact {
    position: absolute;
    left: 400px;
    top: 78px;
    color: var(--purple);
  }
  .contact-name {
    font-weight: 600;
    font-size: 30px;
    color: var(--pink);
    line-height: 1.1;
  }
  .contact-role {
    font-family: "Arimo", sans-serif;
    font-size: 19px;
    margin-bottom: 14px;
  }
  .contact-line {
    font-family: "Arimo", sans-serif;
    font-size: 19px;
    display: flex;
    align-items: center;
    gap: 9px;
    line-height: 1.45;
  }
  .contact-line svg { width: 18px; height: 18px; flex: none; }

  .band-purple {
    position: absolute;
    left: 0; bottom: 0;
    width: 100%;
    height: 22px;
    background: var(--purple);
  }
  .band-pink {
    position: absolute;
    right: 0; bottom: 0;
    width: 282px;
    height: 56px;
    background: var(--pink);
    border-left: 5px solid var(--white);
    border-top: 0;
  }
</style>
</head>
<body>

  <section class="card card-front" aria-label="Card front">
    <div class="brand-disc"></div>
    <p class="brand-name">
      <span class="line-main">Puffy Clouds</span>
      <span class="line-sub">Cotton Candy</span>
    </p>
  </section>

  <section class="card card-back" aria-label="Card back">
    <div class="back-brand">
      <div class="brand-disc"></div>
      <p class="brand-name">
        <span class="line-main">Puffy Clouds</span>
        <span class="line-sub">Cotton Candy</span>
      </p>
    </div>

    <div class="divider"></div>

    <div class="contact">
      <p class="contact-name">Maya Brooks</p>
      <p class="contact-role">Managing Director</p>
      <p class="contact-line">
        <svg viewBox="0 0 24 24" aria-hidden="true"><path fill="var(--pink)" d="M6.6 10.8a15.1 15.1 0 0 0 6.6 6.6l2.2-2.2c.3-.3.7-.4 1-.2 1.1.4 2.3.6 3.6.6.6 0 1 .4 1 1V20c0 .6-.4 1-1 1A17 17 0 0 1 3 4c0-.6.4-1 1-1h3.5c.6 0 1 .4 1 1 0 1.3.2 2.5.6 3.6.1.3 0 .7-.2 1z"/></svg>
        044-555 010 234
      </p>
      <p class="contact-line">
        <svg viewBox="0 0 24 24" aria-hidden="true"><path fill="var(--pink)" d="M2 5h20v14H2z"/><path fill="none" stroke="var(--white)" stroke-width="1.8" d="M2.5 5.5 12 13l9.5-7.5"/></svg>
        hello@puffyclouds.co
      </p>
    </div>

    <div class="band-purple"></div>
    <div class="band-pink"></div>
  </section>

</body>
</html>
```